New Business Card Design Project

Need a design that will create an impact / strong impression towards our clients for our business. We are in the lighting business and we do lighting retrofits for large commercial to industrial clientele.

Target Market(s)

Lighting Industry

Industry/Entity Type

Business

Font styles to use
Other font styles liked:
• we would like to use the font on our logo, not sure what it is though..

Requirements
Must have
• Our logo.
Nice to have
• We are open to suggestions that have to do with lighting.

```html
<!DOCTYPE html>
<html lang="en">
<head>
<meta charset="utf-8">
<title>Lumvaro Retrofit Group – Business Card</title>
<link rel="stylesheet" href="https://fonts.googleapis.com/css2?family=Roboto:wght@400;500;700&display=swap">
<style>
  :root {
    --backdrop: #5b4a3a;
    --forest: #0f3811;
    --leaf: #66be53;
    --leaf-bright: #5cbf46;
    --name-green: #2a9a3c;
    --paper: #f2f2f2;
    --ink-light: #ffffff;
    --logo-green: #14501c;
  }
  * { margin: 0; padding: 0; box-sizing: border-box; }
  html, body {
    width: 1200px; height: 960px; overflow: hidden;
    background: var(--backdrop);
    font-family: "Roboto", Arial, sans-serif;
  }
  .canvas { position: relative; width: 1200px; height: 960px; }
  .card {
    position: absolute; width: 600px; height: 343px; overflow: hidden;
    box-shadow: 2px 3px 4px rgba(0,0,0,0.35);
  }
  .card-front { left: 314px; top: 113px; background: var(--paper); }
  .card-back { left: 311px; top: 472px; background: var(--leaf); }
  .front-shape { position: absolute; inset: 0; }
  .contact-block { position: absolute; left: 33px; top: 34px; color: var(--ink-light); }
  .person-name { font-size: 21px; font-weight: 700; color: var(--name-green); letter-spacing: 0; line-height: 24px; }
  .person-title { font-size: 15px; font-weight: 500; color: var(--leaf-bright); margin-top: 4px; line-height: 18px; }
  .address { font-size: 14.5px; line-height: 18px; margin-top: 12px; }
  .contact-list { list-style: none; margin-top: 8px; }
  .contact-list li { display: flex; align-items: center; font-size: 14.5px; line-height: 19px; }
  .contact-list svg { width: 13px; height: 13px; margin-right: 9px; fill: var(--leaf-bright); flex: none; }
  .brand-front {
    position: absolute; right: 46px; bottom: 52px;
    display: flex; align-items: center; gap: 10px;
    font-size: 26px; font-weight: 700; color: var(--logo-green); letter-spacing: 0.5px;
  }
  .brand-mark { width: 16px; height: 16px; background: var(--leaf-bright); }
  .brand-back {
    position: absolute; left: 0; right: 0; top: 140px; text-align: center;
    font-size: 40px; font-weight: 700; color: var(--ink-light); letter-spacing: 1px;
  }
  .website-back {
    position: absolute; left: 0; right: 0; top: 282px; text-align: center;
    font-size: 14px; color: var(--ink-light); letter-spacing: 2.6px;
  }
</style>
</head>
<body>
<main class="canvas">
  <section class="card card-front">
    <svg class="front-shape" viewBox="0 0 600 343" width="600" height="343" aria-hidden="true">
      <polygon points="0,0 424,0 166,343 0,343" fill="var(--forest)"/>
      <polygon points="424,0 431,0 173,343 166,343" fill="var(--leaf-bright)"/>
    </svg>
    <div class="contact-block">
      <h1 class="person-name">DANIEL REYES</h1>
      <p class="person-title">CEO/FOUNDER</p>
      <p class="address">1420 Aspen Court<br>Fairbanks, Alaska 99701</p>
      <ul class="contact-list">
        <li><svg viewBox="0 0 16 16"><path d="M3 1l3 3-2 2c1 2 3 4 5 5l2-2 3 3-2 3C7 15 1 9 1 3z"/></svg>555 210 4381</li>
        <li><svg viewBox="0 0 16 16"><path d="M4 0h8v16H4zM5.5 2v10h5V2zM7 13.5h2v1H7z" fill-rule="evenodd"/></svg>555 318 7720</li>
        <li><svg viewBox="0 0 16 16"><path d="M4 1h8v4H4zM1 6h14v7h-2v-2H3v2H1zM4 12h8v3H4z"/></svg>555 402 6159</li>
        <li><svg viewBox="0 0 16 16"><path d="M1 3h14v1L8 9 1 4zM1 6l7 5 7-5v7H1z"/></svg>daniel@lumvaro.com</li>
        <li><svg viewBox="0 0 16 16"><circle cx="8" cy="8" r="7"/></svg>www.lumvaro.com</li>
      </ul>
    </div>
    <div class="brand-front"><span class="brand-mark"></span>LUMVARO</div>
  </section>

  <section class="card card-back">
    <p class="brand-back">LUMVARO RETROFIT GROUP</p>
    <p class="website-back">www.lumvaroretrofitgroup.com</p>
  </section>
</main>
</body>
</html>
```